The Polish & Glow Studio Website Update

Hello. I am seeking to freshen up my website with a clean and easy feel that incorporates our modern chic style. Our services cater to mostly young professionals and modern moms.

We focus on natural nail care and gentle professional waxing. We are known for our cleanliness. Our clients like our current website, however I'm hoping to make it look even more professional and user friendly. Some clients have even said our current website feels welcoming, unlike other websites that in they feel give a snobbish vibe. I like clean lines, simple, fresh, and sometimes bold. Totally NOT a fan of whimsical.

I threw added an accent color to the color pallet...however it should be used in moderation. I am also open to other accent colors. I'd like the site to emphasize the Brazilian wax as much as nails, if not more than nail. The photos downloaded are just to give you a few images of who we are, however are not necessary. Current website www.thepolishandglowstudio.example

Target Market(s)

Females 30-55

Industry/Entity Type

Beauty Salon

Coding

Coded - Design and coding required

Number of Pages Required

5+ page

Font styles to use
Sans Serif

Colors
ffffff
1b1b1b
acd136
eeeeee
878787
c4c4c4
efefef
7f7f7f

Requirements
Must have
• Clean look
Nice to have
• Our logo
Should not have
• Whimsical

```html
<!DOCTYPE html>
<html lang="en">
<head>
<meta charset="utf-8">
<title>The Polish &amp; Glow Studio</title>
<link rel="stylesheet" href="https://fonts.googleapis.com/css2?family=Raleway:wght@400;500;600;700;800&family=Open+Sans:ital,wght@0,400;0,600;0,700;1,400&display=swap">
<style>
:root{
  --white:#ffffff;
  --ink:#1b1b1b;
  --lime:#acd136;
  --lime-soft:#b8d94f;
  --mist:#eeeeee;
  --mist-2:#efefef;
  --grey:#878787;
  --grey-2:#7f7f7f;
  --line:#c4c4c4;
  --head:"Raleway",sans-serif;
  --body:"Open Sans",sans-serif;
}
*{margin:0;padding:0;box-sizing:border-box}
html,body{width:1200px;height:4167px;overflow:hidden}
body{background:var(--white);font-family:var(--body);color:var(--ink);position:relative}
section,header,footer{position:absolute;left:0;width:1200px;overflow:hidden}
.photo{position:absolute}

/* Header + hero */
.hero{top:0;height:694px}
.hero .photo{inset:0;background:linear-gradient(100deg,#3a2b26 0%,#7b5a4c 22%,#e2c2ae 40%,#f1e8e3 60%,#f6f5f4 100%)}
.topline{position:absolute;top:0;left:0;width:1200px;height:5px;background:var(--lime)}
.navbar{position:absolute;top:5px;left:0;width:1200px;height:83px;background:rgba(255,255,255,.96)}
.brand{position:absolute;top:5px;left:83px;width:237px;height:120px;background:var(--white);display:flex;align-items:center;justify-content:center;text-align:center;font-family:var(--head);font-weight:600;font-size:24px;line-height:1.15;color:var(--grey-2);box-shadow:0 4px 14px rgba(0,0,0,.08)}
.nav{position:absolute;top:5px;left:400px;height:83px;font-family:var(--head);font-size:15px;font-weight:600;color:var(--ink)}
.nav a{color:inherit;text-decoration:none;position:absolute;top:32px;white-space:nowrap}
.hero-copy{position:absolute;left:811px;top:292px;width:370px}
.hero-kicker{font-family:var(--head);font-weight:600;font-size:29px;color:var(--ink);letter-spacing:.5px;white-space:nowrap}
.hero-title{font-family:var(--head);font-weight:800;font-size:46px;color:var(--lime);margin-top:4px;letter-spacing:.5px;white-space:nowrap}
.hero-text{font-size:14px;color:var(--ink);margin-top:6px;line-height:1.5;width:360px}
.btn{display:inline-flex;align-items:center;justify-content:center;font-family:var(--head);font-weight:700;text-transform:uppercase;letter-spacing:.5px;text-decoration:none}
.btn-lime{background:var(--lime);color:var(--ink)}
.btn-dark{background:var(--ink);color:var(--white)}
.hero .btn{position:absolute;left:814px;top:439px;width:261px;height:53px;font-size:15px}
.dots{position:absolute;left:540px;top:640px;display:flex;gap:22px}
.dots i{width:12px;height:12px;border:2px solid var(--white);border-radius:50%;display:block}
.dots i:nth-child(3){margin-left:40px}

/* Welcome */
.welcome{top:694px;height:445px;background:var(--white)}
.welcome .photo{left:520px;top:0;width:680px;height:445px;background:linear-gradient(100deg,rgba(255,255,255,0) 0%,#f1ddc9 30%,#d9b598 55%,#b9d9e0 75%,#e9eef0 100%);opacity:.85}
.welcome-title{position:absolute;top:40px;width:1200px;text-align:center;font-family:var(--head)}
.welcome-title small{display:block;font-size:24px;font-weight:400;color:var(--grey);letter-spacing:1px}
.welcome-title strong{display:block;font-size:42px;font-weight:800;color:var(--lime);letter-spacing:1px;margin-top:2px}
.welcome p{position:absolute;top:197px;left:222px;width:778px;text-align:center;font-size:14px;line-height:1.6;color:var(--ink)}
.welcome .btn{position:absolute;left:508px;top:298px;width:178px;height:46px;font-size:13px}

/* Appointment band */
.band{top:1139px;height:200px;background:var(--lime);color:var(--white)}
.band h2{position:absolute;left:111px;top:52px;font-family:var(--head);font-weight:700;font-size:31px;letter-spacing:.5px}
.band .note{position:absolute;left:111px;top:100px;font-size:17px;font-style:italic}
.band .hours{position:absolute;left:111px;top:133px;font-size:15px;font-style:italic;display:flex;align-items:center;gap:12px}
.band .btn{position:absolute;left:825px;top:72px;width:255px;height:56px;font-size:14px}

/* Services */
.services{top:1339px;height:1056px;background:var(--white)}
.section-title{position:absolute;width:1200px;text-align:center;font-family:var(--head);font-weight:800;font-size:38px;letter-spacing:1px}
.section-title span{color:var(--lime)}
.services .section-title{top:68px;color:var(--ink)}
.intro{position:absolute;left:230px;width:740px;text-align:center;font-size:13px;line-height:1.7;color:var(--grey)}
.services .intro{top:124px}
.service-row{position:absolute;left:83px;display:flex;gap:10px}
.service{width:250px}
.service .thumb{height:222px}
.service .label{margin-top:14px;height:50px;border:2px solid var(--mist);display:flex;align-items:center;justify-content:center;font-family:var(--head);font-weight:700;font-size:17px;letter-spacing:.5px}
.service .label.active{background:var(--lime);border-color:var(--lime);color:var(--white)}
.service .price{margin-top:12px;text-align:center;font-size:12px;color:var(--grey)}
.service .price b{color:var(--lime);font-size:16px;font-weight:700;margin:0 3px}
.t1{background:linear-gradient(150deg,#d8cfc6,#e6c9a3 55%,#b38a62)}
.t2{background:linear-gradient(150deg,#e8e4e1,#d9a58f 55%,#c7907b)}
.t3{background:linear-gradient(150deg,#f3efeb,#e9cdbf 55%,#c3a592)}
.t4{background:linear-gradient(150deg,#9fd5ec,#4fb7d6 55%,#d9b59b)}
.t5{background:linear-gradient(150deg,#3a2b26,#c89c86 55%,#e8d6cc)}
.t6{background:linear-gradient(150deg,#b14e2e,#e0a489 55%,#f1e6de)}
.t7{background:linear-gradient(150deg,#9fb24a,#e3bba7 55%,#c25f8a)}
.t8{background:linear-gradient(150deg,#e7e1d6,#e8d29f 55%,#f0ece8)}
.services .btn{position:absolute;left:484px;top:961px;width:232px;height:50px;font-size:13px}

/* Gallery */
.gallery{top:2395px;height:544px}
.gallery .bg{inset:0;background:linear-gradient(90deg,#4b4a44 0%,#6b6158 45%,#7d6a60 60%,#4a4843 100%)}
.gallery .section-title{top:50px;color:var(--white)}
.tabs{position:absolute;top:128px;width:1200px;display:flex;justify-content:center;gap:36px;font-family:var(--head);font-weight:700;font-size:14px;color:var(--line);letter-spacing:.5px}
.tabs .on{color:var(--lime)}
.shots{position:absolute;left:83px;top:180px;display:flex}
.shots div{width:259px;height:245px}
.g1{background:linear-gradient(150deg,#bfe3f0,#4aa8c9 50%,#d9b197)}
.g2{background:linear-gradient(150deg,#d9d6cf,#b8b0a2 50%,#8d877d)}
.g3{background:linear-gradient(150deg,#e6e4df,#c9c7bf 50%,#7f8a6f)}
.g4{background:linear-gradient(150deg,#b7a49b,#e3c1ad 50%,#c9a391)}
.arrows{position:absolute;left:570px;top:455px;display:flex;gap:6px}
.arrows span{width:28px;height:28px;background:var(--lime);display:flex;align-items:center;justify-content:center}

/* Testimonials */
.reviews{top:2939px;height:347px;background:var(--white)}
.feed-mark{position:absolute;left:111px;top:92px;width:22px;height:22px;border-radius:50%;background:#d23b3b}
.feed-label{position:absolute;left:143px;top:95px;font-size:14px;color:var(--grey)}
.reviews h3{position:absolute;left:111px;top:150px;font-family:var(--head);font-weight:500;font-size:30px;color:var(--ink)}
.reviews .sub{position:absolute;left:111px;top:200px;width:230px;font-size:12px;line-height:1.5;color:var(--line)}
.avatar{position:absolute;left:500px;top:97px;width:83px;height:83px;border-radius:50%;background:linear-gradient(150deg,#6b5a52,#c4a594)}
.pin-line{position:absolute;left:541px;top:180px;width:2px;height:55px;background:var(--line)}
.pin-dot{position:absolute;left:537px;top:232px;width:10px;height:10px;border-radius:50%;background:var(--line)}
.reviewer{position:absolute;left:610px;top:128px;font-size:16px;color:var(--ink);display:flex;align-items:center;gap:10px}
.reviewer::before{content:"";width:30px;height:1px;background:var(--grey)}
.slide-dots{position:absolute;left:1023px;top:130px;display:flex;gap:14px}
.slide-dots i{width:9px;height:9px;border-radius:50%;background:var(--mist);display:block}
.slide-dots i:first-child{background:var(--lime)}
.quote{position:absolute;left:589px;top:190px;width:494px;font-style:italic;font-size:15px;line-height:1.6;color:var(--ink);text-align:justify}

/* Contact */
.contact{top:3286px;height:436px;background:var(--lime)}
.contact .section-title{top:48px;color:var(--ink)}
.contact .section-title span{color:var(--white)}
.contact .intro{top:108px;color:#6e8a1c;left:110px;width:980px}
.info-row{position:absolute;left:90px;top:186px;display:flex;gap:8px}
.info{width:335px;height:195px;background:var(--lime-soft);display:flex;flex-direction:column;align-items:center;padding-top:34px;color:var(--white)}
.info .k{margin-top:12px;font-size:12px;color:#7f9c2b}
.info .v{margin-top:12px;font-size:18px;font-weight:700;color:var(--ink);text-align:center;line-height:1.3}
.info .v.small{font-size:15px;font-weight:600}

/* Map */
.map{top:3722px;height:209px}
.map .bg{inset:0;background:linear-gradient(120deg,#e3e3e3,#eeeeee 40%,#e6e6e6 70%,#efefef)}
.map .marker{position:absolute;left:580px;top:60px}
.map .place{position:absolute;left:0;width:1200px;top:128px;text-align:center;font-size:16px;font-weight:700;color:var(--ink)}

/* Footer */
.footer{top:3931px;height:236px;background:var(--ink);color:var(--white)}
.socials{position:absolute;left:94px;top:64px;display:flex;gap:16px}
.socials i{width:14px;height:14px;border-radius:50%;background:var(--lime);display:block}
.foot-hours{position:absolute;left:94px;top:108px;font-size:13px;display:flex;align-items:center;gap:10px;color:var(--white)}
.foot-hours b{color:var(--lime)}
.foot-brand{position:absolute;left:0;width:1200px;top:52px;text-align:center;font-family:var(--head);font-weight:600;font-size:30px;line-height:1.1;color:var(--white)}
.copy{position:absolute;right:94px;top:62px;font-size:12px;color:var(--white)}
.foot-links{position:absolute;right:94px;top:108px;display:flex;gap:28px;font-size:13px;color:var(--white)}
.foot-links span{color:var(--grey)}
</style>
</head>
<body>

<header class="hero">
  <div class="photo" role="img" aria-label="Photo of a smiling woman with dark hair and manicured purple nails touching her cheek"></div>
  <div class="topline"></div>
  <div class="navbar"></div>
  <div class="brand">The Polish &amp; Glow<br>Studio</div>
  <nav class="nav">
    <a style="left:17px">Products and Services</a>
    <a style="left:217px">Careers</a>
    <a style="left:328px">Specials</a>
    <a style="left:442px">About Us</a>
    <a style="left:561px">FAQ</a>
    <a style="left:650px">Contact Us</a>
  </nav>
  <div class="hero-copy">
    <div class="hero-kicker">THE BEST NAIL STUDIO</div>
    <div class="hero-title">POLISH &amp; GLOW</div>
    <p class="hero-text">Fresh, gentle care for natural nails and smooth skin, in a calm and clean studio.</p>
  </div>
  <a class="btn btn-lime">Schedule Appointment</a>
  <div class="dots"><i></i><i></i><i></i><i></i></div>
</header>

<section class="welcome">
  <div class="photo" role="img" aria-label="Photo of a relaxed woman in a blue swimsuit with a white flower, lying down"></div>
  <h1 class="welcome-title"><small>WELCOME TO</small><strong>POLISH &amp; GLOW</strong></h1>
  <p>Welcome to a bright, calm studio where natural nail care and gentle waxing come first. Every station is cleaned and reset between guests, every tool is sterilised, and every visit is booked so your time is yours. Relax, unwind and leave feeling polished and fresh.</p>
  <a class="btn btn-lime">&#9656;&nbsp; Know More</a>
</section>

<section class="band">
  <h2>SERVICES BY APPOINTMENT ONLY</h2>
  <p class="note">Salon is only staffed for scheduled appointments.</p>
  <p class="hours">
    <svg width="20" height="20" viewBox="0 0 20 20"><circle cx="10" cy="10" r="8.5" fill="none" stroke="#fff" stroke-width="2"/><path d="M10 5v5l3 2" fill="none" stroke="#fff" stroke-width="2"/></svg>
    DAILY 9am–8pm most days
  </p>
  <a class="btn btn-dark">Schedule Appointment</a>
</section>

<section class="services">
  <h2 class="section-title">OUR <span>SERVICES</span></h2>
  <p class="intro">Design is the method of putting form and content together. Design, just as art, has multiple definitions; there is no single definition. Design can be art. Design can be aesthetics. Design is so simple, that's why it is so complicated.</p>
  <div class="service-row" style="top:231px">
    <div class="service"><div class="thumb t1" role="img" aria-label="Photo of a blonde woman with smooth skin"></div><div class="label">BRAZILIAN WAX</div><div class="price">From<b>30</b>USD</div></div>
    <div class="service"><div class="thumb t2" role="img" aria-label="Photo of manicured hands"></div><div class="label active">WAXING</div><div class="price">From<b>10</b>USD</div></div>
    <div class="service"><div class="thumb t3" role="img" aria-label="Photo of a woman with a facial mask and towel wrap"></div><div class="label">FACIAL &amp; MAKE UP</div><div class="price">From<b>50</b>USD</div></div>
    <div class="service"><div class="thumb t4" role="img" aria-label="Photo of a woman in a blue swimsuit relaxing in the sun"></div><div class="label">BODY &amp; MIND</div><div class="price">From<b>150</b>USD</div></div>
  </div>
  <div class="service-row" style="top:592px">
    <div class="service"><div class="thumb t5" role="img" aria-label="Photo of a dark haired woman with purple nails"></div><div class="label">NAIL CARE</div><div class="price">From<b>30</b>USD</div></div>
    <div class="service"><div class="thumb t6" role="img" aria-label="Photo of a smiling woman with red curly hair"></div><div class="label">WAXING</div><div class="price">From<b>10</b>USD</div></div>
    <div class="service"><div class="thumb t7" role="img" aria-label="Photo of lips and purple manicured fingers"></div><div class="label">FACIAL &amp; MAKE UP</div><div class="price">From<b>50</b>USD</div></div>
    <div class="service"><div class="thumb t8" role="img" aria-label="Photo of a woman with a platinum bob"></div><div class="label">BODY &amp; MIND</div><div class="price">From<b>150</b>USD</div></div>
  </div>
  <a class="btn btn-lime">&#9656;&nbsp; See Our All Services</a>
</section>

<section class="gallery">
  <div class="photo bg" role="img" aria-label="Dimmed background photo of a woman touching her chin"></div>
  <h2 class="section-title">OUR <span>GALLERY</span></h2>
  <div class="tabs"><span class="on">ALL</span><span>STYLES</span><span>SALON</span><span>WAXING</span><span>NAILS</span></div>
  <div class="shots">
    <div class="g1" role="img" aria-label="Photo of a woman in a blue swimsuit"></div>
    <div class="g2" role="img" aria-label="Photo of the salon pedicure chairs"></div>
    <div class="g3" role="img" aria-label="Photo of a treatment room with a waxing bed"></div>
    <div class="g4" role="img" aria-label="Photo of manicured hands"></div>
  </div>
  <div class="arrows">
    <span><svg width="10" height="12" viewBox="0 0 10 12"><path d="M7 1 2 6l5 5" fill="none" stroke="#fff" stroke-width="2"/></svg></span>
    <span><svg width="10" height="12" viewBox="0 0 10 12"><path d="M3 1l5 5-5 5" fill="none" stroke="#fff" stroke-width="2"/></svg></span>
  </div>
</section>

<section class="reviews">
  <span class="feed-mark"></span>
  <span class="feed-label">Review feeds</span>
  <h3>They Love Us</h3>
  <p class="sub">Read what our guests say about their visits with us.</p>
  <div class="avatar" role="img" aria-label="Portrait photo of the reviewer"></div>
  <div class="pin-line"></div><div class="pin-dot"></div>
  <div class="reviewer">Dana Whitford</div>
  <div class="slide-dots"><i></i><i></i><i></i></div>
  <p class="quote">"Ipsum dolor sit amet, consectetur adipiscing elit. Quisque consequat, ex ac commodo gravida, massa ex fringilla augue, eu gravida arcu elit ut est"</p>
</section>

<section class="contact">
  <h2 class="section-title">CONTACT <span>US</span></h2>
  <p class="intro">Design is the method of putting form and content together. Design, just as art, has multiple definitions; there is no single definition. Design can be art. Design can be aesthetics. Design is so simple, that's why it is so complicated.</p>
  <div class="info-row">
    <div class="info">
      <svg width="32" height="30" viewBox="0 0 32 30"><path d="M4 4h24v16H14l-7 6v-6H4z" fill="none" stroke="#fff" stroke-width="2.5" stroke-linejoin="round"/></svg>
      <span class="k">Call</span><span class="v">203-555-0148</span>
    </div>
    <div class="info">
      <svg width="26" height="32" viewBox="0 0 26 32"><path d="M13 1C6.4 1 2 5.8 2 12c0 8 11 19 11 19s11-11 11-19C24 5.8 19.6 1 13 1z" fill="#fff"/><circle cx="13" cy="12" r="4" fill="#b8d94f"/></svg>
      <span class="k">Location</span><span class="v small">42 Linden Street<br>Fairhaven, CT 06500</span>
    </div>
    <div class="info">
      <svg width="32" height="26" viewBox="0 0 32 26"><rect x="2" y="2" width="28" height="22" fill="none" stroke="#fff" stroke-width="2.5"/><path d="M2 3l14 11L30 3" fill="none" stroke="#fff" stroke-width="2.5"/></svg>
      <span class="k">Mail</span><span class="v small">support@polishandglow.example</span>
    </div>
  </div>
</section>

<section class="map">
  <div class="photo bg" role="img" aria-label="Street map around the studio location"></div>
  <svg class="marker" width="40" height="52" viewBox="0 0 40 52"><path d="M20 2C10 2 3 9.5 3 19c0 12 17 31 17 31s17-19 17-31C37 9.5 30 2 20 2z" fill="#acd136"/><circle cx="20" cy="19" r="7" fill="#fff"/></svg>
  <div class="place">Polish and Glow</div>
</section>

<footer class="footer">
  <div class="socials"><i></i><i></i><i></i><i></i><i></i></div>
  <div class="foot-hours">
    <svg width="16" height="16" viewBox="0 0 16 16"><circle cx="8" cy="8" r="7" fill="none" stroke="#acd136" stroke-width="1.6"/><path d="M8 4v4l2.5 1.5" fill="none" stroke="#acd136" stroke-width="1.6"/></svg>
    DAILY &nbsp;—— <b>9am - 8pm</b> most days
  </div>
  <div class="foot-brand">The Polish &amp; Glow<br>Studio</div>
  <div class="copy">© 2016 All Rights Reserved.</div>
  <div class="foot-links">FAQ <span>/</span> Terms <span>/</span> Privacy</div>
</footer>

</body>
</html>
```